Webdesign für Kleingruppenreisen in die Südsteiermark
Zielgruppe
Wir sind ein Start-Up Unternehmen, das als Kleingruppenreisen in die Südsteiermark veranstaltet; der Schwerpunkt liegt auf dem Kulinarischen. Zielgruppe sind Geschäftsleute, die diese Kurzreisen (Do-So) für Marketingzwecke oder als Mitarbeiterbonus (oder auch privat) nutzen möchten.
Aufgabenstellung
Die Homepage soll eine Online-Shop Möglichkeit bieten, in der die Reise (bisher gibt es nur einen Ablauf) gebucht werden kann. Optisch sollte sie sich an das bereits von Ihnen erstellte Logo anlehnen und möglichst ansprechende Fotos von der Südsteiermark, Graz, Leoben usw. enthalten. (Siehe die beiden Flyer und das Logo)
Wir haben inzwischen Bildfreigaben von Haldauer und dem Tourismusverband Kellwinden erhalten und können auch eigene Bilder zur Verfügung stellen. Bitte kontaktieren Sie uns dafür, wenn nötig.

```html
<!DOCTYPE html>
<html lang="de">
<head>
<meta charset="utf-8">
<title>Genusspfad Reisen – Reisen für Feinschmecker</title>
<link href="https://fonts.googleapis.com/css2?family=Kaushan+Script&family=Lato:wght@400;700&family=Montserrat:wght@400&family=Yanone+Kaffeesatz:wght@300;400&display=swap" rel="stylesheet">
<style>
:root{
  --cream:#fdf3ea;
  --page:#fffaf5;
  --card:#fdf2e8;
  --text:#3a3a3a;
  --green:#6aab5c;
  --yellow:#f9c21d;
  --red:#c1161f;
  --accent-red:#d0222a;
  --grey-line:#8a8a8a;
}
*{margin:0;padding:0;box-sizing:border-box}
html,body{width:716px;height:1200px;overflow:hidden}
body{position:relative;background:var(--page);font-family:"Lato",sans-serif;color:var(--text)}
.site-header{position:absolute;left:0;top:0;width:716px;height:113px;background:var(--cream);box-shadow:0 3px 4px rgba(0,0,0,.15)}
.nav-link{position:absolute;top:90px;font-size:8.7px;color:var(--text);text-decoration:none}
.brand{position:absolute;left:272px;top:48px;width:172px;display:flex;align-items:center;gap:5px;justify-content:center}
.brand-dot{width:14px;height:14px;border-radius:50%;background:var(--green)}
.brand-name{font-family:"Lato",sans-serif;font-weight:700;font-size:17px;color:var(--red);white-space:nowrap}
.brand-tag{position:absolute;left:272px;top:68px;width:172px;text-align:center;font-size:6.5px;color:var(--text)}
.social{position:absolute;top:14px;left:530px;display:flex;gap:2px}
.social span{width:14px;height:14px;border-radius:3px;background:var(--yellow)}
.photo{position:absolute;left:0;width:716px}
.photo-hills{top:119px;height:268px;background:linear-gradient(180deg,#a9cfe8 0%,#d6e6ee 40%,#7d9a5a 55%,#4f7a2c 75%,#6f9a2e 100%)}
.photo-wine{top:577px;height:268px;background:linear-gradient(100deg,#d9a57a 0%,#8aa2b0 30%,#6f9a44 60%,#9cb44f 80%,#d8c79b 100%)}
.teaser{position:absolute;left:99px;width:273px;height:112px;background:rgba(250,244,236,.6);box-shadow:0 2px 4px rgba(0,0,0,.15);text-align:center}
.teaser h2{font-family:"Kaushan Script",cursive;font-weight:400;font-size:21px;line-height:25px;color:#2b2b2b;margin-top:12px}
.btn{position:absolute;border-radius:9px;font-family:"Yanone Kaffeesatz",sans-serif;font-size:17px;line-height:31px;color:#fff;text-align:center;box-shadow:0 2px 3px rgba(0,0,0,.25)}
.btn-yellow{left:71px;top:70px;width:131px;height:31px;background:var(--yellow);font-weight:300}
.btn-red{left:58px;top:69px;width:156px;height:31px;background:var(--red)}
.card{position:absolute;width:148px;height:163px;background:var(--card);box-shadow:0 1px 3px rgba(0,0,0,.2);font-size:7.9px;line-height:13px}
.card-icon{position:absolute;left:56px;top:6px;width:36px;height:36px;border-radius:50%;background:#fff;box-shadow:0 1px 3px rgba(0,0,0,.18);display:flex;align-items:center;justify-content:center}
.card-body{position:absolute;left:5px;right:4px;top:49px}
.card-body p+p{margin-top:3px}
.likes{list-style:none;margin-top:2px}
.likes li{display:flex;align-items:center;gap:4px;height:17px}
.divider{position:absolute;left:0;top:1043px;width:716px;height:2px;background:var(--grey-line)}
.newsletter{position:absolute;left:98px;top:1057px;width:520px;height:31px;background:var(--yellow);border-radius:4px}
.nl-field{position:absolute;left:5px;top:4px;width:139px;height:22px;background:#fff;border:1px solid #ddd;display:flex}
.nl-env{width:30px;border-right:1px solid #ddd;display:flex;align-items:center;justify-content:center}
.nl-input{font-size:6.8px;color:#999;line-height:20px;padding-left:14px}
.nl-title{position:absolute;left:172px;top:4px;font-size:11px;color:#fff;font-weight:700}
.nl-sub{position:absolute;left:172px;top:19px;font-size:6.8px;color:#fff}
.foot-col{position:absolute;top:1098px;font-family:"Montserrat",sans-serif;font-size:8.3px;line-height:13px}
.foot-col h3{font-family:"Lato",sans-serif;font-weight:700;font-size:8.3px;color:var(--accent-red);margin-bottom:2px}
.foot-col.phone{font-family:"Lato",sans-serif}
.foot-brand{position:absolute;left:487px;top:1130px;display:flex;align-items:center;gap:5px}
</style>
</head>
<body>

<header class="site-header">
  <a class="nav-link" style="left:143px" href="#">Start</a>
  <a class="nav-link" style="left:197px" href="#">Reise buchen</a>
  <a class="nav-link" style="left:484px" href="#">Kontakt</a>
  <a class="nav-link" style="left:550px" href="#">Impressum</a>
  <div class="brand"><span class="brand-dot"></span><span class="brand-name">Genusspfad Reisen</span></div>
  <div class="brand-tag">Reisen für Feinschmecker in die Steiermark</div>
  <div class="social" aria-label="Soziale Netzwerke"><span></span><span></span><span></span><span></span></div>
</header>

<section class="photo photo-hills" role="img" aria-label="Foto: Weinberge der Südsteiermark mit Klapotetz und Hügellandschaft">
  <div class="teaser" style="top:56px">
    <h2>Haben Sie Geschmack<br>am Besonderen?</h2>
    <a class="btn btn-yellow">Reise buchen</a>
  </div>
</section>

<article class="card" style="left:98px;top:402px">
  <div class="card-icon"><svg width="22" height="22" viewBox="0 0 22 22"><path d="M3 8h6l-1 5a2 2 0 0 1-4 0z" fill="var(--green)"/><rect x="5.5" y="14" width="1" height="5" fill="var(--green)"/><rect x="4" y="19" width="4" height="1" fill="var(--green)"/><rect x="14" y="2" width="2" height="5" fill="var(--green)"/><path d="M13 8h4l1 2v10h-6V10z" fill="var(--green)"/></svg></div>
  <div class="card-body" style="left:13px">
    <p>Lieben Sie...</p>
    <ul class="likes">
      <li><svg width="6" height="8" viewBox="0 0 6 8"><path d="M3 0a3 3 0 0 1 3 3c0 2-3 5-3 5S0 5 0 3a3 3 0 0 1 3-3z" fill="var(--green)"/><circle cx="3" cy="3" r="1" fill="#fff"/></svg>gutes Essen?</li>
      <li><svg width="6" height="8" viewBox="0 0 6 8"><path d="M3 0a3 3 0 0 1 3 3c0 2-3 5-3 5S0 5 0 3a3 3 0 0 1 3-3z" fill="var(--green)"/><circle cx="3" cy="3" r="1" fill="#fff"/></svg>hervorragendes Bier?</li>
      <li><svg width="6" height="8" viewBox="0 0 6 8"><path d="M3 0a3 3 0 0 1 3 3c0 2-3 5-3 5S0 5 0 3a3 3 0 0 1 3-3z" fill="var(--green)"/><circle cx="3" cy="3" r="1" fill="#fff"/></svg>exquisiten Wein?</li>
      <li><svg width="6" height="8" viewBox="0 0 6 8"><path d="M3 0a3 3 0 0 1 3 3c0 2-3 5-3 5S0 5 0 3a3 3 0 0 1 3-3z" fill="var(--green)"/><circle cx="3" cy="3" r="1" fill="#fff"/></svg>kulinarische Spezialitäten?</li>
      <li><svg width="6" height="8" viewBox="0 0 6 8"><path d="M3 0a3 3 0 0 1 3 3c0 2-3 5-3 5S0 5 0 3a3 3 0 0 1 3-3z" fill="var(--green)"/><circle cx="3" cy="3" r="1" fill="#fff"/></svg>und gastfreundliche Menschen?</li>
      <li><svg width="6" height="8" viewBox="0 0 6 8"><path d="M3 0a3 3 0 0 1 3 3c0 2-3 5-3 5S0 5 0 3a3 3 0 0 1 3-3z" fill="var(--green)"/><circle cx="3" cy="3" r="1" fill="#fff"/></svg>wunderschöne Landschaften?</li>
    </ul>
  </div>
</article>

<article class="card" style="left:285px;top:402px">
  <div class="card-icon"><svg width="24" height="18" viewBox="0 0 24 18"><path d="M12 1c3 3 3 10 0 14-3-4-3-11 0-14z" fill="var(--green)"/><path d="M5 5c4 1 6 6 6 10-4-1-6-5-6-10zM19 5c-4 1-6 6-6 10 4-1 6-5 6-10z" fill="var(--green)"/><path d="M1 9c3 0 7 3 9 7-5 0-8-3-9-7zM23 9c-3 0-7 3-9 7 5 0 8-3 9-7z" fill="var(--green)"/></svg></div>
  <div class="card-body">
    <p>Wir glauben, dass unsere Reisen hervorragende Möglichkeiten zum Entspannen und Genießen bieten und sich deshalb besonders gut als „Schmankerl“ für umsatzstarke Kunden, erfolgreiche Mitarbeiter oder einfach für Sie selbst und Ihre Freunde eignen.</p>
  </div>
</article>

<article class="card" style="left:471px;top:402px">
  <div class="card-icon"><svg width="26" height="14" viewBox="0 0 26 14"><path d="M2 4l3 3h6L7 13h3l7-6h5c2 0 3-1 3-1s-1-1-3-1h-5L10 0H7l4 5H5L3 3z" fill="var(--green)" transform="rotate(-8 13 7)"/></svg></div>
  <div class="card-body" style="left:6px">
    <p>Lassen Sie das hektische Berlin und das flache Land für ein paar Tage hinter sich!<br>Die südlichen Ausläufer der Alpen und die sogenannte „steirische Toskana“ sind nur 90 Minuten Direktflug entfernt.</p>
  </div>
</article>

<section class="photo photo-wine" role="img" aria-label="Foto: Weißwein wird in zwei Gläser vor steirischer Landschaft eingeschenkt">
  <div class="teaser" style="top:97px;left:98px">
    <h2>Sind Sie auf den<br>Geschmack gekommen?</h2>
    <a class="btn btn-red">kontaktieren Sie uns</a>
  </div>
</section>

<article class="card" style="left:98px;top:861px">
  <div class="card-icon"><svg width="18" height="22" viewBox="0 0 18 22"><rect x="4" y="2" width="2" height="18" fill="var(--green)"/><path d="M6 2l10 4-10 5z" fill="var(--green)"/><ellipse cx="5" cy="20" rx="4" ry="1.2" fill="var(--green)"/></svg></div>
  <div class="card-body" style="left:7px">
    <p>Lernen Sie Leoben, die Hauptstadt des Haldauer-Bieres kennen und erfahren Sie im Haldauer-Museum die Geschichte dieses weltbekannten Gebräus.</p>
  </div>
</article>

<article class="card" style="left:285px;top:861px">
  <div class="card-icon"><svg width="26" height="26" viewBox="0 0 26 26"><circle cx="13" cy="13" r="6" fill="var(--green)"/><g fill="var(--green)"><path d="M13 0l2 4h-4z"/><path d="M13 26l2-4h-4z"/><path d="M0 13l4 2v-4z"/><path d="M26 13l-4 2v-4z"/><path d="M4 4l4 1.5-2.5 2.5z"/><path d="M22 22l-4-1.5 2.5-2.5z"/><path d="M22 4l-1.5 4-2.5-2.5z"/><path d="M4 22l1.5-4 2.5 2.5z"/></g></svg></div>
  <div class="card-body" style="left:4px">
    <p>Entdecken Sie Graz, die abwechslungs-reiche Landeshauptstadt und Kultur-hauptstadt 2003, mit ihren vielfältigen kulturellen Angeboten, den charmanten Gassen und atemberaubenden Ausblicken.</p>
    <p>Genießen Sie die südlichere Sonne und kosten Sie die ausgezeichneten Weine der Winzer in der Buschenschank.</p>
  </div>
</article>

<article class="card" style="left:471px;top:861px">
  <div class="card-icon"><svg width="24" height="20" viewBox="0 0 24 20"><rect x="3" y="2" width="18" height="6" rx="1" fill="var(--green)"/><rect x="6" y="4" width="12" height="3" fill="#fff"/><rect x="1" y="9" width="22" height="4" fill="var(--green)"/><rect x="1" y="14" width="22" height="4" fill="var(--green)"/></svg></div>
  <div class="card-body" style="left:4px">
    <p>Während unser Exklusiv Transfer Sie zu den Sehenswürdigkeiten bringt, lüftet unser steirischer Reiseleiter für Sie die Geheimnisse seines Heimatlandes, des „grünen Herzens Österreichs“ und führt Sie in erstklassige Restaurants.</p>
    <p>Sie wohnen in ausgesuchten Hotels in zentraler Lage.</p>
  </div>
</article>

<div class="divider"></div>

<form class="newsletter">
  <div class="nl-field">
    <div class="nl-env"><svg width="16" height="11" viewBox="0 0 16 11"><rect x=".5" y=".5" width="15" height="10" fill="none" stroke="var(--yellow)"/><path d="M.5.5l7.5 6 7.5-6" fill="none" stroke="var(--yellow)"/></svg></div>
    <div class="nl-input">Ihre E-Mail Adresse</div>
  </div>
  <div class="nl-title">Newsletter</div>
  <div class="nl-sub">Abonnieren Sie unseren kostenlosen Newsletter und verpasse keine Neuigkeiten</div>
</form>

<footer>
  <div class="foot-col phone" style="left:98px">
    <h3>Telefon</h3>
    <p>XXXXXXXXXXX</p><p>Montag bis Freitag</p><p>von XX bis XX Uhr</p>
  </div>
  <div class="foot-col" style="left:228px">
    <h3>Service</h3>
    <p>Kontakt</p><p>&nbsp;Zahlungsbedingungen</p><p>AGB</p><p>Widerrufsrecht</p><p>Widerrufsformular</p><p>Partnerprogramm</p>
  </div>
  <div class="foot-col" style="left:379px">
    <h3>Informationen</h3>
    <p>Über uns</p><p>Datenschutz</p><p>Impressum</p><p>Newsletter</p>
  </div>
  <div class="foot-brand"><span class="brand-dot"></span><span class="brand-name" style="font-size:15px">Genusspfad Reisen</span></div>
</footer>

</body>
</html>
```